Kestrel Facilities Business Card Design

We would now like to design business cards with the new Kestrel Facilities logo

Target Market(s)

Professional

Industry/Entity Type

Professional services

Contact Information for Business Card

Employee name, title, phone number, email address, corporate office address and logo.

Font styles to use
Sans Serif

Colors
0054AA
0677BA
7BADD7
CADEEF
E8F1F8

Requirements
Must have
• My logo
Should not have
• any other pictures or images besides my logo

```html
<!DOCTYPE html>
<html lang="en">
<head>
<meta charset="utf-8">
<title>Kestrel Facilities Business Card</title>
<link rel="stylesheet" href="https://fonts.googleapis.com/css2?family=Montserrat:wght@400;500;700&display=swap">
<style>
  :root {
    --brand-blue: #3579c0;
    --accent-grey: #a8a8a8;
    --card-white: #ffffff;
    --ink: #1e1e1e;
    --backdrop: #2b2b2b;
    --mark-silver: #dfe3e8;
  }
  * { box-sizing: border-box; margin: 0; padding: 0; }
  html, body {
    width: 1200px; height: 1012px; overflow: hidden;
    background: var(--backdrop);
    font-family: "Montserrat", Arial, sans-serif;
  }
  .canvas { position: relative; width: 1200px; height: 1012px; }
  .card {
    position: absolute; left: 230px; width: 740px; height: 423px;
    box-shadow: 0 12px 30px rgba(0,0,0,.45);
    overflow: hidden;
  }
  .card--back { top: 60px; background: var(--brand-blue); }
  .card--front { top: 529px; background: var(--card-white); }
  .card__frame { position: absolute; inset: 0; }

  .wordmark {
    position: absolute; display: flex; align-items: center; gap: 14px;
    font-weight: 700; letter-spacing: 1px; line-height: 1.1;
  }
  .wordmark__square { width: 34px; height: 34px; flex: none; }
  .card--back .wordmark {
    left: 50%; top: 50%; transform: translate(-50%, -50%);
    color: var(--mark-silver); font-size: 44px;
  }
  .card--back .wordmark__square { background: var(--mark-silver); width: 44px; height: 44px; }
  .card--front .wordmark {
    left: 44px; top: 178px; width: 300px;
    color: var(--brand-blue); font-size: 30px;
  }
  .card--front .wordmark__square { background: var(--brand-blue); }

  .divider {
    position: absolute; left: 362px; top: 110px; width: 1.5px; height: 190px;
    background: var(--brand-blue);
  }
  .contact { position: absolute; left: 392px; top: 104px; color: var(--ink); }
  .contact__name {
    color: var(--brand-blue); font-weight: 700; font-size: 23px; letter-spacing: .3px;
  }
  .contact__title { font-size: 16px; margin-top: 2px; }
  .contact__address { font-size: 16px; margin-top: 20px; line-height: 1.3; }
  .contact__list { list-style: none; margin-top: 20px; font-size: 16px; line-height: 1.45; }
  .contact__list li { display: flex; align-items: center; gap: 8px; }
  .contact__list svg { width: 14px; height: 14px; fill: var(--brand-blue); flex: none; }
</style>
</head>
<body>
<main class="canvas">
  <section class="card card--back" aria-label="Business card back">
    <div class="wordmark"><span class="wordmark__square"></span><span>Kestrel<br>Facilities</span></div>
  </section>

  <section class="card card--front" aria-label="Business card front">
    <svg class="card__frame" viewBox="0 0 740 423" aria-hidden="true">
      <polygon fill="var(--brand-blue)" points="0,0 740,0 740,22 238,22 214,46 0,46"/>
      <polygon fill="var(--accent-grey)" points="222,58 245,36 740,36 740,46 250,46 232,64 222,64"/>
      <polygon fill="var(--brand-blue)" points="0,423 740,423 740,370 560,370 536,396 0,396"/>
      <polygon fill="var(--accent-grey)" points="0,372 528,372 548,352 740,352 740,360 554,360 534,382 0,382"/>
    </svg>

    <div class="wordmark"><span class="wordmark__square"></span><span>Kestrel<br>Facilities</span></div>

    <div class="divider"></div>

    <div class="contact">
      <p class="contact__name">DANA WHITFIELD</p>
      <p class="contact__title">Co-Founder</p>
      <p class="contact__address">4180 N. Harbor Lane<br>Suite 210 Westfield 14</p>
      <ul class="contact__list">
        <li><svg viewBox="0 0 16 16"><path d="M3 1h3l1.5 4-2 1.2a9 9 0 0 0 4.3 4.3L11 8.5l4 1.5v3a2 2 0 0 1-2 2A13 13 0 0 1 1 3a2 2 0 0 1 2-2z"/></svg>+254-300-41762</li>
        <li><svg viewBox="0 0 16 16"><path d="M1 3h14v10H1z M1 3l7 6 7-6" fill="none" stroke="var(--brand-blue)" stroke-width="1.6"/></svg>info@kestrelfacilities.com</li>
        <li><svg viewBox="0 0 16 16"><circle cx="8" cy="8" r="7" fill="none" stroke="var(--brand-blue)" stroke-width="1.5"/><path d="M1 8h14M8 1c3 3 3 11 0 14M8 1c-3 3-3 11 0 14" fill="none" stroke="var(--brand-blue)" stroke-width="1.2"/></svg>www.kestrelfacilities.com</li>
      </ul>
    </div>
  </section>
</main>
</body>
</html>
```